brqnal new business card design project

we need a new business card design. you can view info about us @ brqnal-example.com. i have attached an example of our previous card with our previous name that we no longer use. We really liked the design, colors etc. look below to see more info about this project. it asks for a limited number of words. please see our website for more info about our compnay.

Target Market(s)

law enforcement

Contact Information for Business Card

i have uploaded an example of what we used before that we liked.

Font styles to use
Serif

```html
<!DOCTYPE html>
<html lang="en">
<head>
<meta charset="UTF-8">
<title>BRQNAL Business Card</title>
<link rel="stylesheet" href="https://fonts.googleapis.com/css2?family=Lato:wght@300;400;700&display=swap">
<style>
  :root {
    --page-bg: #e9e7e6;
    --card-light: #f7f5f4;
    --card-dark: #0f1d26;
    --ink-dark: #0f1d26;
    --ink-light: #ffffff;
  }
  * { margin: 0; padding: 0; box-sizing: border-box; }
  html, body {
    width: 1200px;
    height: 900px;
    overflow: hidden;
    background: var(--page-bg);
    font-family: "Lato", sans-serif;
  }
  .business-card {
    position: absolute;
    left: 160px;
    top: 178px;
    width: 880px;
    height: 543px;
    background: var(--card-light);
    box-shadow: 0 10px 30px rgba(0,0,0,0.12);
    overflow: hidden;
  }
  .brand {
    position: absolute;
    top: 0;
    left: 0;
    width: 100%;
    height: 322px;
    text-align: center;
  }
  .brand-name {
    position: absolute;
    top: 96px;
    width: 100%;
    font-weight: 300;
    font-size: 100px;
    line-height: 1;
    letter-spacing: 10px;
    color: var(--ink-dark);
  }
  .brand-tagline {
    position: absolute;
    top: 224px;
    width: 100%;
    font-weight: 400;
    font-size: 22px;
    letter-spacing: 0.5px;
    color: var(--ink-dark);
  }
  .contact-band {
    position: absolute;
    left: 0;
    top: 322px;
    width: 100%;
    height: 221px;
    background: var(--card-dark);
    color: var(--ink-light);
  }
  .person {
    position: absolute;
    right: 472px;
    top: 38px;
    text-align: right;
  }
  .person-name {
    font-weight: 400;
    font-size: 28px;
    letter-spacing: 0.5px;
    line-height: 1.15;
  }
  .person-title {
    font-weight: 400;
    font-size: 23px;
    line-height: 1.2;
  }
  .divider {
    position: absolute;
    left: 440px;
    top: 47px;
    width: 2px;
    height: 84px;
    background: var(--ink-light);
  }
  .contact-list {
    position: absolute;
    left: 468px;
    top: 42px;
    list-style: none;
  }
  .contact-list li {
    display: flex;
    align-items: center;
    height: 32px;
    font-size: 23px;
  }
  .contact-list svg {
    width: 18px;
    height: 18px;
    margin-right: 10px;
    fill: var(--ink-light);
  }
  .address {
    position: absolute;
    top: 150px;
    width: 100%;
    text-align: center;
    font-size: 23px;
  }
</style>
</head>
<body>
  <div class="business-card">
    <header class="brand">
      <div class="brand-name">BRQNAL</div>
      <div class="brand-tagline">LAW ENFORCEMENT INNOVATION</div>
    </header>
    <section class="contact-band">
      <div class="person">
        <div class="person-name">DANIEL MERCER</div>
        <div class="person-title">Managing Director</div>
      </div>
      <div class="divider"></div>
      <ul class="contact-list">
        <li>
          <svg viewBox="0 0 24 24" aria-hidden="true"><path d="M3 8c0-2 4-4 9-4s9 2 9 4v2h-5V8H8v2H3z M6 11h12l2 8H4z M12 13a2.5 2.5 0 1 0 0 5a2.5 2.5 0 1 0 0-5z"/></svg>
          555.014.2290
        </li>
        <li>
          <svg viewBox="0 0 24 24" aria-hidden="true"><path d="M2 5h20v14H2z M4 7v.5l8 6 8-6V7z" fill-rule="evenodd"/></svg>
          info@brqnal-example.com
        </li>
        <li>
          <svg viewBox="0 0 24 24" aria-hidden="true"><path d="M12 2a10 10 0 1 0 0 20a10 10 0 1 0 0-20z M8 7l3 1 1 3-2 2-2-1-2 1-1-3z M14 14l3-1 2 2-3 4-1-2z" fill-rule="evenodd"/></svg>
          www.brqnal-example.com
        </li>
      </ul>
      <div class="address">4120 Ridgeline Avenue Austin, TX 78701</div>
    </section>
  </div>
</body>
</html>
```